Corvane Holdings , new business card design

investment firm with corporate clients . need double sided business card , vertical and horizontal options ,logo must be clear. prefer pantone colors only and sharp design. website also www.corvane.ae

Khalid Bin Tarrafi
Managing Director
Tel. +971 4 387 2940
Mobile +971 50 518 2403
khalid@corvane.ae
Q-Span Plaza, officw 18-B07, Warqa Gardens, Dubai

Contact Information for Business Card

Khalid Bin Tarrafi
Managing Director

Font styles to use
Serif

Colors

Designer to choose colors to be used in the design.

```html
<!DOCTYPE html>
<html lang="en">
<head>
<meta charset="utf-8">
<title>Corvane Holdings — Business Card</title>
<link rel="stylesheet" href="https://fonts.googleapis.com/css2?family=Roboto+Condensed:wght@400;700&family=Roboto:wght@400;500&display=swap">
<style>
  :root {
    --canvas: #e9e7e3;
    --paper: #f6f6f5;
    --ink: #0b0c10;
    --brand-blue: #4a75a0;
    --text-grey: #4a4a4a;
    --rule: #b9b9b9;
    --white: #ffffff;
  }
  * { margin: 0; padding: 0; box-sizing: border-box; }
  html, body { width: 1200px; height: 960px; overflow: hidden; }
  body {
    position: relative;
    background: var(--canvas);
    font-family: "Roboto", Arial, sans-serif;
  }
  .card {
    position: absolute;
    width: 598px;
    height: 344px;
    box-shadow: 0 2px 6px rgba(0,0,0,0.25);
    overflow: hidden;
  }
  .card--front { left: 322px; top: 108px; background: var(--paper); }
  .card--back  { left: 321px; top: 493px; height: 343px; background: var(--ink); }

  .wordmark {
    position: absolute;
    font-family: "Roboto Condensed", Arial, sans-serif;
    font-weight: 400;
    text-transform: uppercase;
    letter-spacing: 5px;
    white-space: nowrap;
  }
  .card--front .wordmark {
    right: 36px; top: 48px;
    font-size: 28px;
    color: var(--ink);
  }
  .card--back .wordmark {
    left: 0; right: 0; top: 150px;
    text-align: center;
    font-size: 34px;
    color: var(--white);
  }

  .holder { position: absolute; left: 38px; top: 176px; }
  .holder__name {
    font-family: "Roboto Condensed", Arial, sans-serif;
    font-weight: 700;
    font-size: 21px;
    color: var(--brand-blue);
    text-transform: uppercase;
    line-height: 1;
  }
  .holder__title {
    margin-top: 8px;
    font-weight: 500;
    font-size: 14.5px;
    color: var(--ink);
    text-transform: uppercase;
  }
  .divider {
    position: absolute; left: 38px; right: 36px; top: 229px;
    height: 1px; background: var(--rule);
  }

  .contacts { position: absolute; left: 38px; top: 246px; list-style: none; }
  .contacts li {
    display: flex; align-items: center;
    height: 19px;
    font-size: 14px;
    color: var(--text-grey);
  }
  .contacts svg { width: 13px; height: 13px; margin-right: 7px; fill: var(--brand-blue); }

  .address {
    position: absolute; right: 36px; top: 266px;
    text-align: right;
    font-size: 14px;
    line-height: 18px;
    color: var(--text-grey);
  }

  .footer-bands { position: absolute; left: 0; top: 0; width: 598px; height: 344px; }
  .website {
    position: absolute; left: 360px; right: 0; top: 319px;
    text-align: center;
    font-size: 13px;
    letter-spacing: 4px;
    color: var(--white);
  }
</style>
</head>
<body>

  <section class="card card--front" aria-label="Business card front">
    <div class="wordmark">Corvane Holdings</div>

    <div class="holder">
      <p class="holder__name">Khalid Bin Tarrafi</p>
      <p class="holder__title">Managing Director</p>
    </div>
    <div class="divider"></div>

    <ul class="contacts">
      <li>
        <svg viewBox="0 0 24 24" aria-hidden="true"><path d="M6.6 10.8a15.2 15.2 0 0 0 6.6 6.6l2.2-2.2c.3-.3.7-.4 1-.2 1.1.4 2.3.6 3.6.6.6 0 1 .4 1 1V20c0 .6-.4 1-1 1A17 17 0 0 1 3 4c0-.6.4-1 1-1h3.5c.6 0 1 .4 1 1 0 1.3.2 2.5.6 3.6.1.3 0 .7-.2 1z"/></svg>
        +971 4 387 2940
      </li>
      <li>
        <svg viewBox="0 0 24 24" aria-hidden="true"><path d="M7 1h10a2 2 0 0 1 2 2v18a2 2 0 0 1-2 2H7a2 2 0 0 1-2-2V3a2 2 0 0 1 2-2zm0 3v14h10V4zm5 15.5a1.2 1.2 0 1 0 0 2.4 1.2 1.2 0 0 0 0-2.4z"/></svg>
        +971 50 518 2403
      </li>
      <li>
        <svg viewBox="0 0 24 24" aria-hidden="true"><path d="M2 5h20v14H2zm2 2v.4l8 5.2 8-5.2V7zm0 2.8V17h16V9.8l-8 5.2z"/></svg>
        khalid@corvane.ae
      </li>
    </ul>

    <address class="address" style="font-style:normal">
      Q-Span Plaza, officw 18-B07<br>
      Warqa Gardens, Dubai
    </address>

    <svg class="footer-bands" viewBox="0 0 598 344" aria-hidden="true">
      <polygon points="0,320 352,320 344,331 0,331" fill="var(--ink)"/>
      <polygon points="0,334 342,334 334,344 0,344" fill="var(--brand-blue)"/>
      <polygon points="358,314 598,314 598,344 346,344" fill="var(--brand-blue)"/>
    </svg>
    <div class="website">www.corvane.ae</div>
  </section>

  <section class="card card--back" aria-label="Business card back">
    <div class="wordmark">Corvane Holdings</div>
  </section>

</body>
</html>
```